Zielgruppe
Immobilienmakler
Aufgabenstellung
Top moderne hochwertige Visitenkate, wir hätten gerne eine sehr hochwertig moderne Visitenkarte mit Bild vom Mitarbeiter... Anbei habe ich die alte Visitenkarte die ich sehr kindlich finde... Es sollte jetzt sehr exklusive aussehen. Alle Daten können von der alten Visitenkarte übernommen werden.. danke

```html
<!DOCTYPE html>
<html lang="de">
<head>
<meta charset="utf-8">
<title>Visitenkarte – Lukas Brunner, Velta Agentur</title>
<link rel="stylesheet" href="https://fonts.googleapis.com/css2?family=Arimo:wght@400;700&display=swap">
<style>
  :root {
    --stage: #000000;
    --card: #ffffff;
    --ink: #000000;
    --brand-green: #2e9550;
    --photo-light: #e9ecef;
    --photo-dark: #8a9099;
  }
  html, body {
    margin: 0;
    padding: 0;
    width: 1200px;
    height: 1200px;
    overflow: hidden;
    background: var(--stage);
  }
  .canvas {
    position: relative;
    width: 1200px;
    height: 1200px;
    background: var(--stage);
    font-family: "Arimo", Arial, sans-serif;
    color: var(--ink);
  }
  .card {
    position: absolute;
    left: 56px;
    top: 246px;
    width: 1087px;
    height: 708px;
    background: var(--card);
    overflow: hidden;
  }
  .portrait-frame {
    position: absolute;
    left: 113px;
    top: 64px;
    width: 192px;
    height: 191px;
    background: var(--brand-green);
  }
  .portrait-photo {
    position: absolute;
    left: 2px;
    top: 1px;
    width: 189px;
    height: 189px;
    border-radius: 50%;
    background: radial-gradient(circle at 50% 40%, var(--photo-light) 0%, #d3d7dc 55%, var(--photo-dark) 100%);
  }
  .rule-vertical {
    position: absolute;
    left: 309px;
    top: 64px;
    width: 3px;
    height: 272px;
    background: var(--ink);
  }
  .rule-horizontal {
    position: absolute;
    left: 113px;
    top: 259px;
    width: 974px;
    height: 5px;
    background: var(--ink);
  }
  .identity {
    position: absolute;
    left: 598px;
    top: 52px;
  }
  .identity .name {
    margin: 0;
    font-weight: 700;
    font-size: 59px;
    line-height: 1;
    letter-spacing: -0.3px;
  }
  .identity .role {
    margin: 10px 0 0;
    font-weight: 400;
    font-size: 29px;
    line-height: 36px;
  }
  .contact {
    position: absolute;
    left: 599px;
    top: 357px;
    display: grid;
    grid-template-columns: 111px auto;
    row-gap: 22px;
    margin: 0;
  }
  .contact dt {
    font-weight: 700;
    font-size: 22px;
    line-height: 24px;
  }
  .contact dd {
    margin: 0;
    font-weight: 400;
    font-size: 22px;
    line-height: 22px;
  }
  .address {
    position: absolute;
    left: 598px;
    top: 572px;
    font-weight: 700;
    font-size: 30px;
    line-height: 34px;
    white-space: nowrap;
  }
  .address .divider {
    display: inline-block;
    width: 3px;
    height: 28px;
    background: var(--ink);
    margin: 0 22px 0 44px;
    vertical-align: -1px;
  }
  .brand {
    position: absolute;
    left: 113px;
    top: 390px;
    font-weight: 700;
    font-size: 54px;
    line-height: 1;
    color: var(--brand-green);
    letter-spacing: -0.5px;
  }
</style>
</head>
<body>
  <div class="canvas">
    <article class="card">
      <div class="portrait-frame">
        <div class="portrait-photo" role="img" aria-label="Porträtfoto von Lukas Brunner im weißen Hemd vor hellem Hintergrund"></div>
      </div>
      <div class="rule-vertical"></div>
      <div class="rule-horizontal"></div>

      <header class="identity">
        <h1 class="name">Lukas Brunner</h1>
        <p class="role">Dipl. Immobilienmanager<br>Geschäftsführer</p>
      </header>

      <div class="brand">Velta Agentur</div>

      <dl class="contact">
        <dt>Telefon</dt><dd>+43 5522 41 870 22</dd>
        <dt>Mobil</dt><dd>+43 664 2841 907</dd>
        <dt>Mail</dt><dd>lukas@velta-agentur.com</dd>
        <dt>Web</dt><dd>www.velta-agentur.com</dd>
      </dl>

      <div class="address">Am Anger 14<span class="divider"></span>6850 Dornbirn</div>
    </article>
  </div>
</body>
</html>
```